Spiritual Healing bussiness needs logo/business card

Simple, clean looking logo/card
For spiritual business with healing services and occult rituals

Contact Information for Business Card

Needs my name: Tobin Varley
Business name: Lantern Healing Shop
Services provided and worded in this way:

Reiki Healing
Tarot
Oils
Rituals Of Change

Can look occult like but with light energy.

Colors
0255a3
3276b5
85abd2
33a6d7
85cae6
0292cd

```html
<!DOCTYPE html>
<html lang="en">
<head>
<meta charset="UTF-8">
<title>Lantern Healing Shop – Business Card</title>
<link rel="stylesheet" href="https://fonts.googleapis.com/css2?family=Arvo&family=Lato:wght@400;700&display=swap">
<style>
  :root {
    --page-bg: #1c1c1e;
    --card-bg: #0f0f10;
    --band-bg: #1a1a1c;
    --band-edge: #222225;
    --rule: #3a3a3e;
    --brand-deep: #0255a3;
    --brand-mid: #3276b5;
    --brand-bright: #0292cd;
    --brand-sky: #33a6d7;
    --text-light: #e9e9ea;
  }
  * { margin: 0; padding: 0; box-sizing: border-box; }
  html, body { width: 1200px; height: 900px; overflow: hidden; }
  body { background: var(--page-bg); font-family: "Lato", sans-serif; position: relative; }

  .card {
    position: absolute;
    width: 560px;
    height: 320px;
    background: var(--card-bg);
    border-radius: 22px;
    overflow: hidden;
    box-shadow: 0 18px 40px rgba(0,0,0,0.55);
  }
  .card--back { left: 90px; top: 80px; }
  .card--front { left: 550px; top: 500px; }

  .card__band {
    position: absolute; left: 0; top: 0; bottom: 0; width: 220px;
    background: linear-gradient(90deg, var(--band-edge) 0 28px, var(--band-bg) 28px 100%);
  }
  .card__band::after {
    content: ""; position: absolute; left: 28px; top: 0; bottom: 0; width: 12px;
    background: #151517;
  }

  .brand__dot {
    display: block; width: 72px; height: 72px; border-radius: 50%;
    border: 6px solid var(--brand-deep);
  }
  .brand__name {
    font-family: "Arvo", serif; color: var(--brand-bright); white-space: nowrap;
  }
  .card__rule { position: absolute; height: 1px; background: var(--rule); }

  /* back side */
  .card--back .brand {
    position: absolute; left: 236px; right: 24px; top: 70px;
    display: flex; flex-direction: column; align-items: center; gap: 14px;
  }
  .card--back .brand__name { font-size: 20px; }
  .card--back .card__rule { left: 236px; right: 24px; top: 232px; }
  .services {
    position: absolute; left: 236px; right: 24px; top: 246px;
    display: flex; align-items: center; justify-content: space-between;
    list-style: none; color: var(--text-light); font-size: 12px; white-space: nowrap;
  }
  .services li { display: flex; align-items: center; gap: 6px; }
  .services li + li::before {
    content: ""; width: 5px; height: 5px; border-radius: 50%; background: var(--brand-bright);
  }

  /* front side */
  .card--front .brand {
    position: absolute; right: 30px; top: 26px;
    display: flex; flex-direction: column; align-items: flex-end; gap: 10px;
  }
  .card--front .brand__dot { margin-right: 72px; }
  .card--front .brand__name { font-size: 22px; }
  .card--front .card__rule { left: 236px; right: 24px; top: 150px; }
  .website {
    position: absolute; right: 30px; top: 164px;
    color: var(--brand-sky); font-size: 16px; white-space: nowrap;
  }
  .contact { position: absolute; left: 46px; bottom: 34px; }
  .contact__name {
    font-family: "Arvo", serif; color: var(--brand-mid); font-size: 24px; margin-bottom: 8px;
  }
  .contact__line {
    display: flex; align-items: center; gap: 9px;
    color: var(--text-light); font-size: 17px; line-height: 1.45; white-space: nowrap;
  }
  .contact__icon { width: 20px; height: 20px; flex: none; }
</style>
</head>
<body>
  <article class="card card--back">
    <div class="card__band"></div>
    <div class="brand">
      <span class="brand__dot"></span>
      <span class="brand__name">Lantern Healing Shop</span>
    </div>
    <div class="card__rule"></div>
    <ul class="services">
      <li>Reiki Healing</li>
      <li>Tarot</li>
      <li>Oils</li>
      <li>Rituals Of Change</li>
    </ul>
  </article>

  <article class="card card--front">
    <div class="card__band"></div>
    <div class="brand">
      <span class="brand__dot"></span>
      <span class="brand__name">Lantern Healing Shop</span>
    </div>
    <div class="card__rule"></div>
    <p class="website">www.LanternHealingShop.com</p>
    <div class="contact">
      <p class="contact__name">Tobin Varley</p>
      <p class="contact__line">
        <svg class="contact__icon" viewBox="0 0 20 20" aria-hidden="true">
          <circle cx="10" cy="10" r="9" fill="none" stroke="#0255a3" stroke-width="1.6"/>
          <path d="M6.5 8.2c0-1 1-1.7 3.5-1.7s3.5.7 3.5 1.7l-1.4.5-.5-1H8.4l-.5 1zM7 10h6l.8 3.2H6.2z" fill="#0255a3"/>
        </svg>
        044-987 650 321
      </p>
      <p class="contact__line">
        <svg class="contact__icon" viewBox="0 0 20 20" aria-hidden="true">
          <circle cx="10" cy="10" r="9" fill="none" stroke="#0255a3" stroke-width="1.6"/>
          <rect x="5.5" y="6.8" width="9" height="6.4" fill="#0255a3"/>
          <path d="M5.5 6.8l4.5 3.6 4.5-3.6" fill="none" stroke="#0f0f10" stroke-width="1"/>
        </svg>
        hello@lanternhealing.com
      </p>
    </div>
  </article>
</body>
</html>
```